business card - Helicopter Flight Services, Flight School, etc.

We need a business card design for a new helicopter service.

We offer Helicopter Flight Services, Aerial Filming & Photography, Flight School, and Helicopter Tours. In that order.

Summit BladeAir, Inc.
Dennis Tollerby
SummitBladeair@Kestmail.com
626-418-7352

Based at the Brenwick Airport in Van Nuys, CA. The final design should communicate integrity and safety. Pictures or logos at your discretion.

Card back side - surprise me.

```html
<!DOCTYPE html>
<html lang="en">
<head>
<meta charset="utf-8">
<title>Summit BladeAir, Inc. – Business Card</title>
<link href="https://fonts.googleapis.com/css2?family=Old+Standard+TT:wght@700&family=Open+Sans:wght@400&display=swap" rel="stylesheet">
<style>
  :root {
    --backdrop: #3a322e;
    --card: #111111;
    --card-edge: #1c1c1c;
    --ink: #ffffff;
    --ink-soft: #d6d6d6;
    --rule-accent: #5a5a9a;
    --divider: #8a8a8a;
  }
  html, body {
    margin: 0;
    padding: 0;
    width: 1200px;
    height: 780px;
    overflow: hidden;
    background: var(--backdrop);
  }
  .canvas {
    position: relative;
    width: 1200px;
    height: 780px;
  }
  .card {
    position: absolute;
    top: 235px;
    width: 520px;
    height: 310px;
    background: var(--card);
    border: 1px solid var(--card-edge);
    border-radius: 4px;
    box-shadow: 0 10px 28px rgba(0,0,0,0.45);
    color: var(--ink);
  }
  .card--front { left: 50px; }
  .card--back { left: 630px; }

  .brand-name {
    font-family: "Old Standard TT", Georgia, serif;
    font-weight: 700;
    color: var(--ink);
    margin: 0;
    white-space: nowrap;
  }
  .card--front .brand-name {
    position: absolute;
    top: 52px;
    left: 0;
    right: 0;
    text-align: center;
    font-size: 29px;
  }
  .title-rule {
    position: absolute;
    top: 102px;
    left: 36px;
    right: 36px;
    height: 1px;
    background: var(--rule-accent);
  }
  .holder-name {
    position: absolute;
    top: 148px;
    left: 50px;
    font-family: "Open Sans", Arial, sans-serif;
    font-size: 14px;
    color: var(--ink-soft);
  }
  .contact-divider {
    position: absolute;
    top: 140px;
    left: 220px;
    width: 1px;
    height: 100px;
    background: var(--divider);
  }
  .contact-list {
    position: absolute;
    top: 146px;
    left: 238px;
    margin: 0;
    padding: 0;
    list-style: none;
    font-family: "Open Sans", Arial, sans-serif;
    font-size: 13px;
    line-height: 19px;
    color: var(--ink-soft);
  }
  .contact-item {
    display: flex;
    align-items: flex-start;
    gap: 8px;
  }
  .contact-icon {
    flex: none;
    width: 12px;
    height: 12px;
    margin-top: 3px;
  }
  .contact-text--indent { padding-left: 20px; }

  .card--back .brand-name {
    position: absolute;
    top: 112px;
    left: 0;
    right: 0;
    text-align: center;
    font-size: 36px;
  }
  .services {
    position: absolute;
    top: 162px;
    left: 0;
    right: 0;
    text-align: center;
    font-family: "Old Standard TT", Georgia, serif;
    font-weight: 700;
    font-size: 15px;
    color: var(--ink);
    margin: 0;
  }
</style>
</head>
<body>
<main class="canvas">
  <section class="card card--front" aria-label="Card front">
    <h1 class="brand-name">Summit BladeAir, Inc.</h1>
    <div class="title-rule"></div>
    <p class="holder-name" style="margin:0">Dennis Tollerby</p>
    <div class="contact-divider"></div>
    <ul class="contact-list">
      <li class="contact-item">
        <svg class="contact-icon" viewBox="0 0 12 12" aria-hidden="true">
          <rect width="12" height="12" rx="2" fill="#fff"/>
          <path d="M3.5 2.8 L5 2.8 L5.4 4.6 L4.6 5.2 Q5.4 6.8 6.8 7.4 L7.4 6.6 L9.2 7 L9.2 8.5 Q5 9 3.5 2.8Z" fill="#111"/>
        </svg>
        <span>626-418-7352</span>
      </li>
      <li class="contact-item">
        <svg class="contact-icon" viewBox="0 0 12 12" aria-hidden="true">
          <rect width="12" height="12" rx="2" fill="#fff"/>
          <rect x="2.5" y="3.5" width="7" height="5" fill="none" stroke="#111" stroke-width="1"/>
          <path d="M2.5 3.5 L6 6.3 L9.5 3.5" fill="none" stroke="#111" stroke-width="1"/>
        </svg>
        <span>SummitBladeair@Kestmail.com</span>
      </li>
      <li class="contact-item">
        <svg class="contact-icon" viewBox="0 0 12 12" aria-hidden="true">
          <rect width="12" height="12" rx="2" fill="#fff"/>
          <path d="M6 2.2 A2.6 2.6 0 0 1 8.6 4.8 Q8.6 6.6 6 9.6 Q3.4 6.6 3.4 4.8 A2.6 2.6 0 0 1 6 2.2Z" fill="#111"/>
          <circle cx="6" cy="4.8" r="0.9" fill="#fff"/>
        </svg>
        <span>2740 W. Larkhaven Ave. Ste.B</span>
      </li>
      <li class="contact-item contact-text--indent">Corvale, CA 91487</li>
    </ul>
  </section>

  <section class="card card--back" aria-label="Card back">
    <h2 class="brand-name">Summit BladeAir, Inc.</h2>
    <p class="services">Airport · Tour guide · Heliport</p>
  </section>
</main>
</body>
</html>
```